MRT Property - Business Cards

Looking for a business card & general letterhead, signage etc design for our new logo.

Colours:
000a20
0056a2
00b5ef
0088ce
68cef2

Fonts:
Poppins
Karla

Please keep look and feel of new brand - example in the zip package I sent.

```html
<!DOCTYPE html>
<html lang="en">
<head>
<meta charset="utf-8">
<title>MRT Property – Business Cards</title>
<link href="https://fonts.googleapis.com/css2?family=Montserrat:wght@400;500;800&family=Kalam:wght@400&display=swap" rel="stylesheet">
<style>
  :root {
    --backdrop: #999999;
    --paper: #ffffff;
    --brand-blue: #0a56a5;
    --brand-navy: #1e3a72;
    --ink: #1b1b1b;
    --icon-blue: #1a73bd;
  }
  * { box-sizing: border-box; margin: 0; padding: 0; }
  html, body { width: 1093px; height: 1200px; overflow: hidden; }
  body {
    background: var(--backdrop);
    font-family: "Montserrat", sans-serif;
    position: relative;
  }
  .card {
    position: absolute;
    left: 264px;
    width: 581px;
    height: 364px;
    border-radius: 20px;
    overflow: hidden;
  }
  .card-front { top: 225px; background: var(--paper); }
  .card-back { top: 616px; background: var(--brand-blue); }

  .brand-name {
    position: absolute;
    left: 23px;
    top: 28px;
    font-family: "Montserrat", sans-serif;
    font-weight: 800;
    color: var(--brand-blue);
    line-height: 1;
  }
  .brand-name .primary { display: block; font-size: 46px; letter-spacing: 1px; }
  .brand-name .secondary { display: block; font-size: 46px; letter-spacing: 1px; }

  .holder {
    position: absolute;
    right: 35px;
    top: 24px;
    text-align: right;
  }
  .holder-name {
    font-family: "Kalam", cursive;
    font-size: 26px;
    color: var(--brand-blue);
    line-height: 1.1;
  }
  .holder-role {
    font-size: 13px;
    font-weight: 500;
    color: var(--ink);
    letter-spacing: 0.2px;
  }
  .accent-bar {
    position: absolute;
    right: 0;
    top: 26px;
    width: 20px;
    height: 47px;
    background: var(--brand-blue);
  }

  .address {
    position: absolute;
    left: 24px;
    top: 201px;
    font-size: 13.5px;
    line-height: 16px;
    color: var(--ink);
  }
  .contacts {
    position: absolute;
    left: 25px;
    top: 266px;
    list-style: none;
  }
  .contacts li {
    display: flex;
    align-items: center;
    gap: 9px;
    height: 25px;
    font-size: 13px;
    color: var(--ink);
  }
  .contacts svg { width: 14px; height: 14px; fill: var(--icon-blue); flex: none; }

  .back-brand {
    position: absolute;
    left: 0;
    right: 0;
    top: 140px;
    text-align: center;
    font-family: "Montserrat", sans-serif;
    font-weight: 800;
    font-size: 54px;
    letter-spacing: 2px;
    color: var(--brand-navy);
  }
</style>
</head>
<body>
  <section class="card card-front">
    <div class="brand-name">
      <span class="primary">MRT</span>
      <span class="secondary">PROPERTY</span>
    </div>

    <div class="holder">
      <p class="holder-name">Daniel Carter</p>
      <p class="holder-role">Managing Director</p>
    </div>
    <div class="accent-bar"></div>

    <address class="address" style="font-style:normal">
      240 Cedar Ridge Lane<br>
      Clinton, MS 39056
    </address>

    <ul class="contacts">
      <li>
        <svg viewBox="0 0 24 24" aria-hidden="true"><path d="M6.6 10.8a15 15 0 0 0 6.6 6.6l2.2-2.2c.3-.3.7-.4 1-.2 1.1.4 2.3.6 3.6.6.6 0 1 .4 1 1V20c0 .6-.4 1-1 1A17 17 0 0 1 3 4c0-.6.4-1 1-1h3.5c.6 0 1 .4 1 1 0 1.3.2 2.5.6 3.6.1.3 0 .7-.2 1z"/></svg>
        <span>555.210.4417</span>
      </li>
      <li>
        <svg viewBox="0 0 24 24" aria-hidden="true"><path d="M2 5h20v14H2zm2 2v.5l8 5 8-5V7z"/></svg>
        <span>info@mrtproperty.com</span>
      </li>
      <li>
        <svg viewBox="0 0 24 24" aria-hidden="true"><circle cx="12" cy="12" r="10"/></svg>
        <span>www.mrtproperty.com</span>
      </li>
    </ul>
  </section>

  <section class="card card-back">
    <p class="back-brand">MRT PROPERTY</p>
  </section>
</body>
</html>
```